Business cards for Zestcycle

We need a business card layout for our new bike and e-bike rental (we also sell used e-bikes and bike accessories). The logo already exists.

```html
<!DOCTYPE html>
<html lang="en">
<head>
<meta charset="utf-8">
<title>Zestcycle business cards</title>
<link href="https://fonts.googleapis.com/css2?family=Roboto+Condensed:wght@300;400;700&display=swap" rel="stylesheet">
<style>
  :root {
    --bg: #e9e7e3;
    --paper: #f6f6f4;
    --slate: #2f4b51;
    --slate-deep: #223c43;
    --mint: #66c9b0;
    --ink: #2b3a3d;
    --white: #ffffff;
  }
  * { box-sizing: border-box; margin: 0; padding: 0; }
  html, body { width: 1200px; height: 886px; overflow: hidden; }
  body {
    background: var(--bg);
    font-family: "Roboto Condensed", Arial, sans-serif;
    position: relative;
  }
  .card {
    position: absolute;
    top: 293px;
    width: 520px;
    height: 300px;
    overflow: hidden;
    box-shadow: 0 6px 18px rgba(0,0,0,0.18);
  }
  .card-front { left: 60px; background: var(--paper); }
  .card-back  { left: 620px; background: linear-gradient(135deg, #35535a, var(--slate) 60%, #2b464c); }

  .front-panels { position: absolute; inset: 0; }

  .brand { position: absolute; left: 70px; top: 38px; text-align: right; }
  .brand-mark {
    width: 34px; height: 34px; border-radius: 50%;
    border: 3px solid var(--ink);
    margin: 0 auto 6px 60px;
  }
  .brand-name {
    font-weight: 300; font-size: 52px; letter-spacing: 1px;
    color: var(--mint); line-height: 1;
  }
  .brand-tagline {
    font-weight: 700; font-size: 13px; color: var(--ink); margin-top: 4px;
  }

  .contact {
    position: absolute; right: 18px; top: 168px;
    color: var(--white); font-size: 14px; line-height: 22px; text-align: right;
  }
  .contact-row { display: flex; justify-content: flex-end; align-items: center; gap: 8px; }
  .contact-row svg { width: 12px; height: 12px; fill: none; stroke: var(--white); stroke-width: 1.6; }

  .person {
    position: absolute; left: 54px; top: 214px;
    color: var(--white);
  }
  .person-name { font-weight: 700; font-size: 19px; line-height: 1.1; letter-spacing: 0.5px; }
  .person-role { font-size: 13px; line-height: 1.25; }
  .person-address { font-weight: 300; font-size: 12.5px; line-height: 1.3; }

  .back-brand { position: absolute; left: 40px; top: 168px; color: var(--white); }
  .back-name { font-weight: 400; font-size: 42px; letter-spacing: 1px; line-height: 1; }
  .back-tagline { font-weight: 700; font-size: 12px; margin-top: 4px; }
  .back-services { font-weight: 400; font-size: 13px; line-height: 1.3; margin-top: 6px; }
</style>
</head>
<body>

<section class="card card-front" aria-label="Business card front">
  <svg class="front-panels" width="520" height="300" viewBox="0 0 520 300" aria-hidden="true">
    <polygon points="300,150 520,150 520,300 350,300 300,200" fill="var(--slate-deep)"/>
    <polygon points="0,200 300,200 350,300 0,300" fill="var(--mint)"/>
  </svg>

  <div class="brand">
    <div class="brand-mark"></div>
    <div class="brand-name">ZESTCYCLE</div>
    <div class="brand-tagline">ride easy, ride far</div>
  </div>

  <div class="contact">
    <div class="contact-row">604 215 7781
      <svg viewBox="0 0 12 12"><path d="M2 1.5 L4.5 1.5 L5.5 4 L4 5 Q5 7.5 7 8 L8 6.5 L10.5 7.5 L10.5 10 Q4 10.5 2 1.5 Z"/></svg>
    </div>
    <div class="contact-row">917 352 4068
      <svg viewBox="0 0 12 12"><rect x="3" y="1" width="6" height="10" rx="1"/></svg>
    </div>
    <div class="contact-row">mara@zestcycle.com
      <svg viewBox="0 0 12 12"><rect x="1" y="2.5" width="10" height="7"/><path d="M1 2.5 L6 6.5 L11 2.5"/></svg>
    </div>
    <div class="contact-row">www.zestcycle.com
      <svg viewBox="0 0 12 12"><circle cx="6" cy="6" r="5"/><path d="M1 6 H11 M6 1 Q3 6 6 11 Q9 6 6 1"/></svg>
    </div>
  </div>

  <div class="person">
    <div class="person-name">MARA LINDQVIST</div>
    <div class="person-role">CEO/FOUNDER</div>
    <div class="person-address">2140 Juniper Road<br>Fairbanks, Alaska 99701</div>
  </div>
</section>

<section class="card card-back" aria-label="Business card back">
  <div class="back-brand">
    <div class="back-name">ZESTCYCLE</div>
    <div class="back-tagline">ride easy, ride far</div>
    <div class="back-services">New bike &amp; e-bike rental<br>We also sell used e-bikes &amp;<br>bike accessories</div>
  </div>
</section>

</body>
</html>
```